Whitcombe Business Card Design

The name of the business is Dario Whitcombe, CPA LLC
The service that we offer is Accounting, Tax & Consulting Services. I need it to have the following items:
Dario Whitcombe, Principal
Phone Number
Email Address
Physical Address

I have attached the company logo, one in black and one in white. Please provide a design in black background and the other in white background. Please include "Accounting, Tax & Consulting Services". I want the business card to be clean and very professional.

```html
<!DOCTYPE html>
<html lang="en">
<head>
<meta charset="utf-8">
<title>Dario Whitcombe, CPA LLC — Business Cards</title>
<link href="https://fonts.googleapis.com/css2?family=Montserrat:wght@400;500;600;700;800&display=swap" rel="stylesheet">
<style>
  :root {
    --backdrop: #e9e9ea;
    --card-dark: #1c1c1d;
    --card-light: #ffffff;
    --brand-red: #9b1c20;
    --ink: #1d1d1f;
    --ink-soft: #8a8a8d;
    --ink-dim: #6f6f72;
  }
  * { box-sizing: border-box; margin: 0; padding: 0; }
  html, body { width: 1200px; height: 988px; overflow: hidden; }
  body {
    background: var(--backdrop);
    font-family: "Montserrat", sans-serif;
    position: relative;
  }
  .card {
    position: absolute;
    left: 250px;
    width: 700px;
    height: 400px;
    box-shadow: 0 10px 30px rgba(0,0,0,.18);
    overflow: hidden;
  }
  /* Front: dark */
  .card--front { top: 60px; background: var(--card-dark); }
  .front-lockup {
    position: absolute;
    left: 120px; top: 150px;
    display: flex; align-items: center; gap: 22px;
  }
  .brand-square {
    width: 64px; height: 64px;
    background: var(--brand-red);
  }
  .front-name {
    font-weight: 600;
    font-size: 32px;
    letter-spacing: 1px;
    text-transform: uppercase;
    color: var(--ink-soft);
  }
  .front-tagline {
    position: absolute;
    left: 206px; top: 232px;
    font-weight: 700;
    font-size: 17px;
    color: var(--ink-dim);
  }

  /* Back: light */
  .card--back { top: 528px; background: var(--card-light); }
  .back-lockup {
    position: absolute;
    left: 150px; top: 48px;
    display: flex; align-items: center; gap: 12px;
  }
  .back-lockup .brand-square { width: 30px; height: 30px; }
  .back-name {
    font-weight: 600;
    font-size: 18px;
    letter-spacing: .5px;
    text-transform: uppercase;
    color: var(--ink);
  }
  .principal {
    position: absolute;
    left: 150px; top: 130px;
    font-weight: 800;
    font-size: 24px;
    color: var(--brand-red);
    text-transform: uppercase;
  }
  .rule {
    position: absolute;
    left: 150px; right: 60px; top: 172px;
    height: 2px;
    background: var(--brand-red);
  }
  .contacts {
    position: absolute;
    left: 0; top: 200px;
    list-style: none;
  }
  .contact {
    display: flex; align-items: center;
    height: 44px; margin-bottom: 6px;
  }
  .contact-tab {
    width: 120px; height: 42px;
    background: var(--brand-red);
    border-radius: 0 10px 10px 0;
    display: flex; align-items: center; justify-content: flex-end;
    padding-right: 22px;
  }
  .contact-tab svg { width: 20px; height: 20px; }
  .contact-text {
    margin-left: 20px;
    font-size: 18px;
    font-weight: 500;
    color: var(--ink);
  }
  .address {
    position: absolute;
    right: 40px; top: 218px;
    font-style: normal;
    font-size: 17px;
    font-weight: 500;
    line-height: 1.55;
    color: var(--ink);
    text-align: left;
  }
</style>
</head>
<body>

  <section class="card card--front" aria-label="Business card front">
    <div class="front-lockup">
      <span class="brand-square"></span>
      <span class="front-name">Dario Whitcombe, CPA LLC</span>
    </div>
    <p class="front-tagline">Accounting, Tax &amp; Consulting Services</p>
  </section>

  <section class="card card--back" aria-label="Business card back">
    <div class="back-lockup">
      <span class="brand-square"></span>
      <span class="back-name">Dario Whitcombe, CPA LLC</span>
    </div>

    <h1 class="principal">Dario Whitcombe, Principal</h1>
    <div class="rule"></div>

    <ul class="contacts">
      <li class="contact">
        <span class="contact-tab">
          <svg viewBox="0 0 24 24" fill="#fff" aria-hidden="true"><path d="M6.6 10.8a15.2 15.2 0 0 0 6.6 6.6l2.2-2.2c.3-.3.7-.4 1-.2 1.1.4 2.3.6 3.6.6.6 0 1 .4 1 1V20c0 .6-.4 1-1 1A17 17 0 0 1 3 4c0-.6.4-1 1-1h3.5c.6 0 1 .4 1 1 0 1.3.2 2.5.6 3.6.1.3 0 .7-.2 1z"/></svg>
        </span>
        <span class="contact-text">555-214-7390</span>
      </li>
      <li class="contact">
        <span class="contact-tab">
          <svg viewBox="0 0 24 24" aria-hidden="true"><rect x="3" y="6" width="18" height="12" fill="#fff"/><path d="M3 6l9 7 9-7" fill="none" stroke="#9b1c20" stroke-width="1.6"/></svg>
        </span>
        <span class="contact-text">info@dariowhitcombecpa.com</span>
      </li>
      <li class="contact">
        <span class="contact-tab">
          <svg viewBox="0 0 24 24" fill="none" stroke="#fff" stroke-width="1.8" aria-hidden="true"><circle cx="12" cy="12" r="9"/><ellipse cx="12" cy="12" rx="4" ry="9"/><path d="M3 12h18"/></svg>
        </span>
        <span class="contact-text">www.dariowhitcombecpa.com</span>
      </li>
    </ul>

    <address class="address">Lakeview Centre 2180 Harbor<br>Crest Blvd Suite 310</address>
  </section>

</body>
</html>
```